We need a logo design that explain all the products we possess.
The main goal is to represent graphically all the logos, pointing to one single logo - Vellamor.
The descriptions are in french.
I have uploaded a file with 4 logos to use:
Vellamor (the logo that all the rest should be pointing to)
RTN
Ombrevik
TroupéLune
All logo must be used in the vector graphic format, the description file is in each folder, it's the description that should be next to the logo.

The main goal of this is to create a banner 10' x 11' (estimated)

Target Market(s)

Cities

Requirements
Must have
• All the logos in the zip file in vector graphic.
Nice to have
• A background
Should not have
• Do not use KOL logo, it's a mix with RTN, and Kol Blue/dark blue with inscription "RTN", Charging fees for a part of the picture is not ok!

```html
<!DOCTYPE html>
<html lang="fr">
<head>
<meta charset="utf-8">
<title>Portail Vellamor 2.0</title>
<link rel="stylesheet" href="https://fonts.googleapis.com/css2?family=Exo+2:wght@400;600;800&display=swap">
<style>
  :root {
    --stage: #c6c6c6;
    --paper: #ececec;
    --brand-blue: #4a90cb;
    --deep-blue: #1f6db5;
    --cyan: #0aa8e8;
    --red: #d4463f;
    --red-light: #e55a50;
    --green: #7cbd45;
    --green-light: #9ccf5f;
    --gold: #e0a20c;
    --gold-light: #f3bd16;
    --ink: #222222;
    --white: #ffffff;
  }
  html, body {
    margin: 0;
    padding: 0;
    width: 1200px;
    height: 1200px;
    overflow: hidden;
    background: var(--stage);
  }
  .banner {
    display: block;
    width: 1092px;
    height: 1200px;
    margin: 0 auto;
  }
  .brand-name {
    font-family: "Exo 2", sans-serif;
    font-weight: 800;
    fill: var(--white);
  }
  .tagline {
    font-family: "Exo 2", sans-serif;
    font-weight: 600;
    fill: var(--white);
  }
  .tagline .version { fill: var(--red); }
  .product-name {
    font-family: "Exo 2", sans-serif;
    font-weight: 600;
  }
  .description {
    font-family: "Exo 2", sans-serif;
    font-weight: 400;
    fill: var(--ink);
  }
</style>
</head>
<body>
<svg class="banner" viewBox="237 165 1456 1600" xmlns="http://www.w3.org/2000/svg">
  <defs>
    <radialGradient id="ring-red" cx="40%" cy="35%" r="70%">
      <stop offset="0" stop-color="var(--red-light)"/>
      <stop offset="1" stop-color="var(--red)"/>
    </radialGradient>
    <radialGradient id="ring-green" cx="40%" cy="35%" r="70%">
      <stop offset="0" stop-color="var(--green-light)"/>
      <stop offset="1" stop-color="var(--green)"/>
    </radialGradient>
    <radialGradient id="ring-gold" cx="40%" cy="35%" r="70%">
      <stop offset="0" stop-color="var(--gold-light)"/>
      <stop offset="1" stop-color="var(--gold)"/>
    </radialGradient>
  </defs>

  <!-- paper -->
  <rect class="paper" x="237" y="165" width="1456" height="1600" fill="var(--paper)"/>
  <rect class="top-band" x="237" y="165" width="1456" height="15" fill="var(--brand-blue)"/>

  <!-- hub -->
  <path class="hub" d="M466 165 H1467 V495 A500.5 500.5 0 0 1 466 495 Z" fill="var(--brand-blue)"/>
  <path class="hub-orbit" d="M484 598 A490 490 0 0 0 1450 598" fill="none" stroke="var(--white)" stroke-width="14"/>
  <path class="hub-orbit" d="M484 598 A490 490 0 0 0 1450 598" fill="none" stroke="var(--deep-blue)" stroke-width="6"/>

  <g class="orbit-end">
    <circle cx="484" cy="598" r="35" fill="var(--white)"/>
    <circle cx="484" cy="598" r="29" fill="none" stroke="var(--deep-blue)" stroke-width="5"/>
    <circle cx="484" cy="598" r="20" fill="var(--cyan)"/>
  </g>
  <g class="orbit-end">
    <circle cx="1450" cy="598" r="35" fill="var(--white)"/>
    <circle cx="1450" cy="598" r="29" fill="none" stroke="var(--deep-blue)" stroke-width="5"/>
    <circle cx="1450" cy="598" r="20" fill="var(--cyan)"/>
  </g>

  <text class="brand-name" x="966" y="690" text-anchor="middle" font-size="96" letter-spacing="4">VELLAMOR</text>
  <text class="tagline" x="963" y="815" text-anchor="middle" font-size="50">Portail Vellamor <tspan class="version">2.0</tspan></text>

  <!-- connectors -->
  <g class="connector" stroke="var(--deep-blue)" stroke-width="3">
    <line x1="634" y1="898" x2="580" y2="1008"/>
    <line x1="953" y1="1016" x2="953" y2="1150"/>
    <line x1="1253" y1="935" x2="1307" y2="1022"/>
  </g>
  <g class="nodes" stroke="var(--white)" stroke-width="4">
    <circle cx="644" cy="880" r="16" fill="var(--red)"/>
    <circle cx="953" cy="1000" r="16" fill="var(--green)"/>
    <circle cx="1241" cy="917" r="16" fill="var(--gold)"/>
    <circle cx="578" cy="1013" r="8" fill="var(--red)"/>
    <circle cx="955" cy="1155" r="8" fill="var(--green)"/>
    <circle cx="1310" cy="1027" r="8" fill="var(--gold)"/>
  </g>

  <!-- dashed orbits -->
  <g class="dash-orbit" fill="none" stroke="var(--deep-blue)" stroke-width="4" stroke-dasharray="16 10">
    <path d="M386 1063 A200 200 0 0 1 722 1185"/>
    <path d="M778 1288 A200 200 0 0 1 1133 1252"/>
    <path d="M1207 1200 A200 200 0 0 1 1535 1057"/>
  </g>

  <!-- product: Ombrevik -->
  <g class="product">
    <circle cx="526" cy="1205" r="177" fill="url(#ring-red)"/>
    <circle cx="526" cy="1205" r="146" fill="var(--white)"/>
    <text class="product-name" x="526" y="1220" text-anchor="middle" font-size="44" fill="var(--deep-blue)">Ombrevik</text>
  </g>

  <!-- product: TroupéLune -->
  <g class="product">
    <circle cx="965" cy="1355" r="177" fill="url(#ring-green)"/>
    <circle cx="965" cy="1355" r="146" fill="var(--white)"/>
    <text class="product-name" x="965" y="1370" text-anchor="middle" font-size="42" fill="var(--deep-blue)">TroupéLune</text>
  </g>

  <!-- product: RTN -->
  <g class="product">
    <circle cx="1405" cy="1205" r="177" fill="url(#ring-gold)"/>
    <circle cx="1405" cy="1205" r="146" fill="var(--white)"/>
    <text class="product-name" x="1405" y="1222" text-anchor="middle" font-size="52" fill="var(--deep-blue)">RTN</text>
  </g>

  <!-- descriptions -->
  <g class="checklist">
    <g fill="none" stroke="var(--red)" stroke-width="3">
      <circle cx="419" cy="1441" r="20"/>
      <polyline points="409,1441 417,1449 430,1433"/>
      <circle cx="419" cy="1505" r="20"/>
      <polyline points="409,1505 417,1513 430,1497"/>
      <circle cx="419" cy="1568" r="20"/>
      <polyline points="409,1568 417,1576 430,1560"/>
      <circle cx="419" cy="1640" r="20"/>
      <polyline points="409,1640 417,1648 430,1632"/>
    </g>
    <text class="description" x="460" y="1456" font-size="42">Permis</text>
    <text class="description" x="460" y="1522" font-size="42">Carte</text>
    <text class="description" x="460" y="1584" font-size="42">Inventaire</text>
    <text class="description" x="460" y="1655" font-size="42">Taxes</text>
  </g>
  <text class="description" x="957" y="1606" text-anchor="middle" font-size="42">Licences pour</text>
  <text class="description" x="957" y="1656" text-anchor="middle" font-size="42">animaux</text>
  <text class="description" x="1403" y="1456" text-anchor="middle" font-size="42">Conseil sans</text>
  <text class="description" x="1403" y="1504" text-anchor="middle" font-size="42">papier</text>

  <!-- footer band -->
  <path class="footer-band" d="M370 1765 Q375 1745 400 1745 H1200 L1193 1765 Z" fill="var(--red)"/>
  <path class="footer-band" d="M1193 1765 L1200 1745 H1530 Q1555 1745 1560 1765 Z" fill="var(--brand-blue)"/>
</svg>
</body>
</html>
```